Modellprojekt in der Jugendhilfe sucht für Abschlussbroschüre ansprechendes Design
Zielgruppe
Wir sind ein Jugendhilfeträger und haben kürzlich ein dreijähriges Modellprojekt 'Prüfzeichen-Mitbestimmte Familienbegleitung' (Signet 'PZ_Zertifizierung' liegt anbei) beendet. Zielgruppen sind zum Einen Kinder und Jugendliche, die in Erziehungshilfe-Wohngruppen leben und zum Anderen Fach- und Führungskräfte in der Kinder- und Jugendhilfe. Über Ablauf und Schlussfolgerungen aus dem abgeschlossenen Modellprojekt soll eine 30-seitige Broschüre mit dem Titel 'Hier wächst Mitsprache' Untertitel 'Ein Wegbericht zum Prüfzeichen' Auskunft geben.
Aufgabenstellung
- Broschüre im DIN A4 - Format,
- Dummy-Text für Projektstruktur und -beteiligte,
- Formschönes und dynamisches Design,
- Platzhalter für eigene Bilder (max. 3 pro Seite),
- die 6 Einrichtungslogos in einer Reihe auf dem Deckblatt vorne (unten),
- Der Broschüreninhalt ist in der PDF 'Kurzvorstellung enthalten',
- Vorgaben zum CD im PDF 'Hauptmanual KWB',
- Das KWB-Signet, wie im Manual beschrieben,
- das ebenfalls hochgeladene Gütesiegel kommt auf das Deckblatt

```html
<!DOCTYPE html>
<html lang="de">
<head>
<meta charset="utf-8">
<title>Hier wächst Mitsprache – Broschüre</title>
<link rel="stylesheet" href="https://fonts.googleapis.com/css2?family=Fira+Sans:wght@400;500&family=Noto+Serif:wght@400&display=swap">
<style>
  :root {
    --blue: #1d6fb5;
    --green: #3aaa35;
    --grey-dark: #9b9b9b;
    --grey-light: #dcdcdc;
    --text: #333333;
    --paper: #ffffff;
    --stage: #ececec;
    --sans: "Fira Sans", Arial, sans-serif;
    --serif: "Noto Serif", Georgia, serif;
  }
  html, body { margin: 0; padding: 0; }
  body {
    width: 1200px; height: 848px; overflow: hidden;
    background: var(--stage); position: relative;
    font-family: var(--sans); color: var(--text);
  }
  .page { position: absolute; background: var(--paper); overflow: hidden; }

  /* Spread */
  .spread { left: 390px; top: 51px; width: 758px; height: 537px; }
  .spread-photo {
    position: absolute; left: 10px; top: 12px; width: 358px; height: 241px;
    background: radial-gradient(circle at 22% 30%, #f6d27e 0%, #e3a24a 35%, #b8774a 65%, #7d6a5a 100%);
  }
  .spread-title {
    position: absolute; left: 40px; top: 272px; margin: 0;
    font-weight: 400; font-size: 20.5px; line-height: 24px; color: var(--blue);
  }
  .spread-sub {
    position: absolute; left: 40px; top: 328px; margin: 0;
    font-size: 8.5px; color: var(--blue);
  }
  .col {
    position: absolute; font-family: var(--serif); font-size: 4.6px;
    line-height: 8.2px; color: var(--text);
  }
  .col p { margin: 0 0 6px; }
  .col h3 {
    margin: 0 0 6px; font-family: var(--serif); font-weight: 400;
    font-size: 6.4px; line-height: 8px; color: var(--blue);
  }
  .col ul { margin: 0 0 6px; padding: 0; list-style: none; }
  .col li { position: relative; padding-left: 6px; margin-bottom: 2px; }
  .col li::before { content: "›"; position: absolute; left: 0; color: var(--blue); font-weight: 700; }
  .col-a { left: 14px; top: 362px; width: 140px; }
  .col-b { left: 191px; top: 362px; width: 140px; }
  .col-c { left: 432px; top: 206px; width: 148px; }
  .col-d { left: 585px; top: 206px; width: 148px; }
  .col-d2 { left: 585px; top: 384px; width: 148px; }

  .chart-title { position: absolute; left: 432px; top: 50px; font-size: 6.4px; }
  .donut { position: absolute; top: 62px; width: 100px; height: 100px; }
  .donut-1 { left: 444px; }
  .donut-2 { left: 602px; }
  .pct { position: absolute; font-size: 6.2px; }
  .legend { position: absolute; top: 167px; display: flex; gap: 6px; font-size: 5px; }
  .legend span::before {
    content: ""; display: inline-block; width: 4px; height: 4px; margin-right: 2px;
    vertical-align: 0; background: var(--c);
  }
  .spread-photo-small {
    position: absolute; left: 585px; top: 274px; width: 173px; height: 104px;
    background: linear-gradient(120deg, #5d6a73 0%, #b89a86 40%, #8f7b70 65%, #cfd3d6 100%);
  }
  .folio {
    position: absolute; top: 512px; font-size: 3.8px; color: #888;
  }
  .folio b { color: var(--blue); font-weight: 400; }

  /* Cover */
  .cover { left: 57px; top: 213px; width: 402px; height: 570px; }
  .cover-photo {
    position: absolute; left: 0; top: 0; width: 402px; height: 310px;
    background: linear-gradient(135deg, #6f96ad 0%, #3c5f86 35%, #c9a58a 55%, #2e4e7c 80%, #9fb6c4 100%);
  }
  .seal {
    position: absolute; left: 54px; top: 54px; width: 62px; height: 62px;
    border-radius: 50%; background: #1e6b63; border: 3px solid #6dbf4a; box-sizing: border-box;
  }
  .cover-title {
    position: absolute; left: 56px; top: 366px; margin: 0;
    font-weight: 500; font-size: 22.5px; line-height: 29px; color: var(--blue);
  }
  .partners { position: absolute; left: 56px; top: 475px; width: 320px; height: 70px; }
  .partner { position: absolute; display: flex; align-items: center; gap: 3px;
    font-size: 5px; line-height: 6px; font-weight: 500; color: var(--text); }
  .partner i { display: inline-block; width: 8px; height: 8px; background: #e8692c; flex: none; }
  .partner i.round { border-radius: 50%; }
  .lead { top: 0; left: 0; font-size: 6px; line-height: 7.4px; font-weight: 400; }
  .lead i { width: 26px; height: 56px; background: #8ea6cf; }
</style>
</head>
<body>

<section class="page spread" aria-label="Innenseiten 4 und 5">
  <div class="spread-photo" role="img" aria-label="Foto: zwei Hände reichen einander im warmen Gegenlicht, mit handschriftlichem Zitat"></div>

  <h2 class="spread-title">Hier wächst Mitsprache –<br>ein Wegbericht zum Prüfzeichen</h2>
  <p class="spread-sub">Text steht hier als Platzhalter</p>

  <div class="col col-a">
    <h3>Ut enim ad minim veniam quis nostrud</h3>
    <p>Voluptatur sitatio nsenis molorem rempos quo magnamus nus porectem faccae vero modit, nonestrum rectatis alita estinve rberspe roresendit litionsed quam autat sciistia consequi doluptatur?</p>
    <p>Mollab ipsandest aut hil ilita core es int, is iur as nis debitem eris eat ipsume rem poressunt in reped que verferae nessitem quo od ese vollaut deliquas eos sectium sum eum sumenis reped ut ma consequid quibus si alit ad eumque nulpa nobis natur? Sus dis sectium salit ad sunt harum ium nobis natur?</p>
  </div>

  <div class="col col-b">
    <ul>
      <li>Tet mincium quunt destium quasped qui to test volo ese sa volorum volorep erspiciam que et ratiunt es que offic tecabor emporit voluptas ut volorpo reptaturis ea sum que debis es nobit omnis re volorepelest qui quiandestion pro tem.</li>
      <li>Endae es re estionet quiandam, volut pe veliquaturit lam quibus reritat escipsam ant ipsa sit vendendania ideriant deremperum voluptat.</li>
    </ul>
    <p>Bus di unt od mos venet qui inia si aut impel im facerspit de molores re nos perumquam, offic torporem as eaquis sequam, te sitissi tem derum expel molorepre laborrovidem ari quia num aut laut facienit, ut quibusc ientores rectur simus doluptatem eventius est eat eum sa quam quo blab id ut dunt, eicid quo quo quid quas is illant etur?</p>
  </div>

  <div class="chart-title">Tertio derunt bleurtns vertuliert der</div>

  <svg class="donut donut-1" viewBox="0 0 100 100" aria-label="Ringdiagramm 12, 76 und 32 Prozent">
    <circle cx="50" cy="52" r="36" fill="none" stroke="var(--grey-light)" stroke-width="10"/>
    <circle cx="50" cy="52" r="36" fill="none" stroke="var(--green)" stroke-width="10"
      stroke-dasharray="27 999" transform="rotate(-90 50 52)"/>
    <circle cx="50" cy="52" r="36" fill="none" stroke="var(--grey-dark)" stroke-width="10"
      stroke-dasharray="56 999" transform="rotate(180 50 52)"/>
  </svg>
  <span class="pct" style="left:524px;top:82px">12 %</span>
  <span class="pct" style="left:546px;top:120px">76 %</span>
  <span class="pct" style="left:422px;top:96px">32 %</span>

  <svg class="donut donut-2" viewBox="0 0 100 100" aria-label="Ringdiagramm 22, 44 und 66 Prozent">
    <circle cx="50" cy="52" r="36" fill="none" stroke="var(--grey-light)" stroke-width="10"/>
    <circle cx="50" cy="52" r="36" fill="none" stroke="var(--green)" stroke-width="10"
      stroke-dasharray="38 999" transform="rotate(-90 50 52)"/>
    <circle cx="50" cy="52" r="36" fill="none" stroke="var(--grey-dark)" stroke-width="10"
      stroke-dasharray="113 999" transform="rotate(90 50 52)"/>
  </svg>
  <span class="pct" style="left:682px;top:82px">22 %</span>
  <span class="pct" style="left:704px;top:120px">44 %</span>
  <span class="pct" style="left:590px;top:96px">66 %</span>

  <div class="legend" style="left:432px">
    <span style="--c:var(--green)">Lorem serunt</span>
    <span style="--c:var(--grey-light)">Pertuoe lerase</span>
    <span style="--c:var(--grey-dark)">Bello tertio</span>
  </div>
  <div class="legend" style="left:585px">
    <span style="--c:var(--green)">Lorem serunt</span>
    <span style="--c:var(--grey-light)">Pertuoe lerase</span>
    <span style="--c:var(--grey-dark)">Bello tertio</span>
  </div>

  <div class="col col-c">
    <h3>Ra cumquis ex et aciamendi doluptatet adissit ilita eatiis sim sinctur?</h3>
    <p>Eliquis vel et eniscia es repe cuscium que volo volorio eum quam, consequi ium laborestium qui rae volectecae cum volore volorem et dolum eiunt plia dolut aut re aspel evenetum apient omnim vendemoditas esersperum ut latempor modisqu iatem. Millaut unt. Mus sit ea doluptam, cus sundiat emperferum, am apicab ime nonet ad most ipsanditam quidisse verume ium et ea volum alit fugit que num consequia dessit, ne videl int magnieturit, ipsapero cone vent eatque corepudit laceatuscim de ommo et laut qui dolore cusae.</p>
    <p>Imagnis si dunti voluptassed experibus nimint restibu sandenistore labo. At ad quasped ut quam il ius dolupta epellam rero odiamet urestibus maiorat.</p>
    <p>Qui dem es excesto tatescitam, ulluptis diae veniaepelit alitae non eaqui untis volupta speres event, qui nonemquibus ullam quiam autem. Sam ex et, sit et audandi aectur? At quo dolumque voluptatur sinctis nus sed est magnissinus exerfer spiendi cum aut alibusanim everume res sim quam rem re rem alia vollut maxima consenimus.</p>
    <p>Aquo doloria voloriam, vellupt atiumqu idionecestet ressenimi, cullit quam quatiur aut rendit adit occusam quo dundantius ab ium fugition reptat labor mo ipsunt quae imus doluptatum ipsae corero id qui reptatius.</p>
  </div>

  <div class="col col-d">
    <p>Volum aspeles es estisqui quae veles aut lab in cum que dus eicipsandit ad quatium quae essincietur ipsam et et od qui aut aut adigendelit lit aut esequae. Ectis sitate sundit, omnis demporrum ea vellaut exero di omni nobitam nam nest, incturiae sedigendio tem ipsum iliquam quia quae pore santem volupit issendia volorpo remamusam, et entur aliquidipis que post parcia natur.</p>
  </div>
  <div class="spread-photo-small" role="img" aria-label="Foto: Jugendliche sitzen lachend zusammen vor einem Gebäude"></div>
  <div class="col col-d2">
    <p>Nimodipsant. Demoles explaut aris eos sequide doluptae et quibusanda id maio is desti iniet aut quia vel il magnieturit essum ut utassequels ut volorro videst, illibus velendaeped mos molorum dolestiae. Ibus con pere eum rescips aperia verum velluptat que num consequia dessit, ne videl int magnieturit, ips.</p>
    <h3>Udae ma quossus eosandus inctotas moloruptat.</h3>
    <p>Nullecus. Di volupti nimagnis et a sit latet velia quia si bero eaquiasi te volorestota perorro occab ipsundebis.</p>
  </div>

  <div class="folio" style="left:20px">Hier wächst Mitsprache – Wege zum Prüfzeichen</div>
  <div class="folio" style="left:688px">Hier wächst Mitsprache – Wege zum Prüfzeichen &nbsp;<b>| 5</b></div>
</section>

<section class="page cover" aria-label="Titelseite">
  <div class="cover-photo" role="img" aria-label="Foto: viele Hände liegen übereinander in der Mitte eines Kreises"></div>
  <div class="seal" role="img" aria-label="Prüfzeichen"></div>

  <h1 class="cover-title">Hier wächst Mitsprache –<br>Wege zum Prüfzeichen</h1>

  <div class="partners">
    <div class="partner lead"><i></i><span>Verbund<br>Küstenwerk<br>Begleitung</span></div>
    <div class="partner" style="left:95px;top:10px"><i></i><span>Fördeverbund<br>Kinderhilfe Nord</span></div>
    <div class="partner" style="left:170px;top:10px"><i class="round"></i><span>Jugendwerk<br>Eiderland</span></div>
    <div class="partner" style="left:240px;top:14px"><i></i><span>Jugendhilfe Geestland</span></div>
    <div class="partner" style="left:95px;top:42px"><i style="background:#f2b705"></i><span>Kinderhäuser<br>am Seeufer</span></div>
    <div class="partner" style="left:170px;top:42px"><i class="round" style="background:#d9322a"></i><span>Hilfen<br>Marschland</span></div>
    <div class="partner" style="left:240px;top:42px"><i></i><span>Familienhilfe<br>Holmertal</span></div>
  </div>
</section>

</body>
</html>
```